PYLON SIGN FOR “MEADOWLARK CAR WASH SPRINT”

please see the new images in my brief. I have a logo design and the colors I would like you to follow.

please put "meadowlark car wash sprint" in the logo

Target Market(s)

GENERAL PUBLIC

Industry/Entity Type

CAR WASH

Font styles to use
Other font styles liked:
• CURSIVE AND BLOCK LETTERING BOTH AS IN THE SAMPLE PIC

Colors
00AB8E
00BBA5
67D7C9
C6EFE9
E9F9F6
6B429C
8869AF
B7A5CE
E3DAEB
F3F0F8

Requirements
Must have
• 1. “MEADOWLARK CAR WASH SPRINT” PLEASE PUT THIS IN THE LOGO 2. USE BLACK, WHITE, GREEN AND SILVER FOR A COLOR
Nice to have
• I WOULD LIKE TO SEE THE SIGN IN BOTH COLOR THEMES: WHITE, BLACK, GREEN AND SILVER AND WHITE BLACK PURPLE AND SILVER

```html
<!DOCTYPE html>
<html lang="en">
<head>
<meta charset="utf-8">
<title>Meadowlark Car Wash Sprint – Pylon Sign</title>
<link rel="stylesheet" href="https://fonts.googleapis.com/css2?family=Michroma&family=Russo+One&display=swap">
<style>
  :root {
    --page-bg: #d3d3d3;
    --sign-deep: #07120b;
    --sign-green: #15391f;
    --sign-blue: #0d1e2a;
    --lime-top: #b4ef1a;
    --lime-bottom: #4fa80a;
    --silver-light: #ffffff;
    --silver-mid: #bfc4c8;
    --silver-dark: #8d9398;
    --bubble-tone: #7fc41c;
  }
  * { margin: 0; padding: 0; box-sizing: border-box; }
  html, body {
    width: 830px;
    height: 1200px;
    overflow: hidden;
    background: var(--page-bg);
  }
  .canvas {
    position: relative;
    width: 830px;
    height: 1200px;
  }
  .pylon-sign {
    position: absolute;
    left: 35px;
    top: 316px;
    width: 760px;
    height: 568px;
    overflow: hidden;
    background:
      radial-gradient(ellipse at 30% 35%, var(--sign-green) 0%, transparent 60%),
      radial-gradient(ellipse at 80% 75%, var(--sign-blue) 0%, transparent 55%),
      radial-gradient(ellipse at 65% 20%, #102b22 0%, transparent 50%),
      var(--sign-deep);
    box-shadow: 0 10px 22px rgba(0,0,0,0.35);
  }
  .bubble-corner {
    position: absolute;
  }
  .bubble-corner--left {
    left: 0; top: 0;
    width: 80px; height: 190px;
    background: radial-gradient(ellipse at 20% 30%, rgba(127,196,28,0.28), rgba(200,205,210,0.12) 45%, transparent 75%);
  }
  .bubble-corner--right {
    right: 0; top: 0;
    width: 250px; height: 130px;
    background: radial-gradient(ellipse at 60% 25%, rgba(200,205,210,0.22), rgba(127,196,28,0.15) 45%, transparent 75%);
  }
  .brand-mark {
    position: absolute;
    left: 0; right: 0;
    top: 150px;
    display: flex;
    align-items: center;
    justify-content: center;
    gap: 12px;
  }
  .brand-mark__dot {
    width: 18px; height: 18px;
    border-radius: 50%;
    background: var(--bubble-tone);
  }
  .brand-mark__name {
    font-family: "Russo One", sans-serif;
    font-size: 24px;
    color: var(--silver-mid);
    letter-spacing: 1px;
  }
  .headline {
    position: absolute;
    left: 0; top: 0;
    width: 760px; height: 568px;
  }
  .headline text { font-weight: 400; }
  .headline__primary { font-family: "Russo One", sans-serif; }
  .headline__secondary, .headline__tertiary { font-family: "Michroma", sans-serif; }
</style>
</head>
<body>
<main class="canvas">
  <section class="pylon-sign" aria-label="Meadowlark Car Wash Sprint pylon sign">
    <div class="bubble-corner bubble-corner--left" role="img" aria-label="Soap bubble decoration"></div>
    <div class="bubble-corner bubble-corner--right" role="img" aria-label="Soap bubble decoration"></div>

    <div class="brand-mark">
      <span class="brand-mark__dot"></span>
      <span class="brand-mark__name">MEADOWLARK CAR WASH SPRINT</span>
    </div>

    <svg class="headline" viewBox="0 0 760 568" aria-label="Meadowlark Car Wash Sprint">
      <defs>
        <linearGradient id="lime-fill" x1="0" y1="0" x2="0" y2="1">
          <stop offset="0" stop-color="var(--lime-top)"/>
          <stop offset="0.5" stop-color="#8fd814"/>
          <stop offset="1" stop-color="var(--lime-bottom)"/>
        </linearGradient>
        <linearGradient id="silver-fill" x1="0" y1="0" x2="0" y2="1">
          <stop offset="0" stop-color="var(--silver-light)"/>
          <stop offset="0.55" stop-color="var(--silver-mid)"/>
          <stop offset="1" stop-color="var(--silver-dark)"/>
        </linearGradient>
      </defs>
      <text class="headline__primary" x="380" y="348" text-anchor="middle"
            font-size="118" textLength="626" lengthAdjust="spacingAndGlyphs"
            fill="url(#lime-fill)">MEADOWLARK</text>
      <text class="headline__secondary" x="380" y="449" text-anchor="middle"
            font-size="66" textLength="618" lengthAdjust="spacingAndGlyphs"
            fill="url(#silver-fill)">CAR WASH</text>
      <text class="headline__tertiary" x="380" y="513" text-anchor="middle"
            font-size="50" textLength="440" lengthAdjust="spacingAndGlyphs"
            fill="url(#lime-fill)">SPRINT</text>
    </svg>
  </section>
</main>
</body>
</html>
```